Business Card Design

We need a business card designed for our new company. Prefer a black card with white logo & writing.

Contact Information for Business Card

Ted Galloway, address: 7-4812 Fernhollow Road, Abbotsford, BC, V3K 8R2, Office Phone: 604-712-3390, Cell: 604-947-2164, Email: ted@resinworkshub.ca

Colors

Designer to choose only greyscale colors for use in the design.

```html
<!DOCTYPE html>
<html lang="en">
<head>
<meta charset="utf-8">
<title>Resin Works Hub — Business Card</title>
<link rel="stylesheet" href="https://fonts.googleapis.com/css2?family=Poppins:wght@300;400;700&display=swap">
<style>
  :root {
    --backdrop: #2b2b2c;
    --card: #1d1d1f;
    --card-edge: #151516;
    --ink: #f4f4f4;
    --ink-soft: #c9c9c9;
    --rule: #8a8a8a;
    --emboss: #262628;
    --emboss-light: #2f2f32;
  }
  * { box-sizing: border-box; margin: 0; padding: 0; }
  html, body {
    width: 1200px; height: 780px; overflow: hidden;
    background: var(--backdrop);
    font-family: "Poppins", sans-serif;
    color: var(--ink);
  }
  .stage {
    width: 1200px; height: 780px;
    display: flex; align-items: center; justify-content: center; gap: 40px;
  }
  .card {
    position: relative;
    width: 540px; height: 309px;
    background: var(--card);
    border-radius: 4px;
    box-shadow: 0 2px 0 var(--card-edge), 0 14px 30px rgba(0,0,0,.45);
    overflow: hidden;
  }

  /* front */
  .brand {
    position: absolute; left: 40px; top: 70px; width: 210px;
    display: flex; flex-direction: column; align-items: center; gap: 10px;
  }
  .brand-mark { width: 22px; height: 22px; border-radius: 50%; background: var(--ink); }
  .brand-name {
    font-weight: 700; font-size: 27px; line-height: 1.05;
    text-align: center; letter-spacing: .5px; text-transform: uppercase;
  }
  .address {
    position: absolute; left: 40px; bottom: 26px;
    font-size: 12.5px; font-weight: 400; letter-spacing: .2px;
  }
  .divider {
    position: absolute; left: 282px; top: 62px;
    width: 1px; height: 170px; background: var(--rule);
  }
  .contact { position: absolute; left: 312px; top: 62px; }
  .person-name { font-size: 30px; line-height: 1.05; font-weight: 300; }
  .person-name strong { font-weight: 700; }
  .person-role { font-size: 13px; font-weight: 400; color: var(--ink-soft); margin: 2px 0 14px; }
  .contact-list { list-style: none; display: flex; flex-direction: column; gap: 5px; }
  .contact-list li {
    display: flex; align-items: center; gap: 9px;
    font-size: 13px; font-weight: 400; letter-spacing: .2px;
  }
  .contact-list svg { width: 13px; height: 13px; flex: none; }

  /* back */
  .card-back { display: flex; align-items: center; justify-content: center; }
  .brand-emboss {
    display: flex; flex-direction: column; align-items: center; gap: 12px;
  }
  .brand-emboss .brand-mark { background: var(--emboss-light); width: 26px; height: 26px; }
  .brand-emboss .brand-name {
    color: var(--emboss-light); font-size: 38px;
  }
</style>
</head>
<body>
<main class="stage">
  <section class="card card-front" aria-label="Business card front">
    <div class="brand">
      <span class="brand-mark"></span>
      <p class="brand-name">Resin Works<br>Hub</p>
    </div>
    <p class="address">7-4812 Fernhollow Road, Abbotsford, BC, V3K 8R2.</p>
    <span class="divider"></span>
    <div class="contact">
      <h1 class="person-name"><strong>Ted</strong> Galloway</h1>
      <p class="person-role">Founder &amp; CEO</p>
      <ul class="contact-list">
        <li>
          <svg viewBox="0 0 16 16" fill="var(--ink)"><path d="M3.6 1.2l2.3 2.6-1.3 1.6c.9 2 2.4 3.5 4.4 4.4l1.6-1.3 2.6 2.3-1.2 2.1C6.7 12.6 3.4 9.3 1.5 2.4z"/></svg>
          604-712-3390
        </li>
        <li>
          <svg viewBox="0 0 16 16" fill="none" stroke="var(--ink)" stroke-width="1.6"><rect x="4" y="1.5" width="8" height="13" rx="1.5"/><line x1="7" y1="12" x2="9" y2="12"/></svg>
          604-947-2164
        </li>
        <li>
          <svg viewBox="0 0 16 16" fill="none" stroke="var(--ink)" stroke-width="1.4"><circle cx="8" cy="8" r="6.3"/><ellipse cx="8" cy="8" rx="2.7" ry="6.3"/><line x1="1.7" y1="8" x2="14.3" y2="8"/></svg>
          www.resinworkshub.ca
        </li>
        <li>
          <svg viewBox="0 0 16 16" fill="none" stroke="var(--ink)" stroke-width="1.5"><rect x="1.5" y="3.5" width="13" height="9" rx="1"/><polyline points="1.8,4 8,9 14.2,4"/></svg>
          ted@resinworkshub.ca
        </li>
      </ul>
    </div>
  </section>

  <section class="card card-back" aria-label="Business card back">
    <div class="brand-emboss">
      <span class="brand-mark"></span>
      <p class="brand-name">Resin Works<br>Hub</p>
    </div>
  </section>
</main>
</body>
</html>
```